Fee Detective - Website Design

Create website designs for new FeeDetective.com web application.
We are looking for a clean, playful design based on the attached wireframes and the images we have collected on our PinVault board for inspiration : https://app.pinvault-example.net/7QrTb2kZw4Xc81?p=3Hyd9mLe5Rf
Users of the site will want to be able to quickly run a search using the transaction descriptor they want to identify and see any matching merchants. If they don't get a match then we need then to be able to easily provide further details so we can try and find a match for them
Target Market(s)
Anyone with a bank account
Number of Pages Required
5+ page
Requirements
Must have
- Clean yet playful design, incorporating the themes from our pinvault board

```html
<!DOCTYPE html>
<html lang="en">
<head>
<meta charset="utf-8">
<title>Fee Detective – Website Design</title>
<link href="https://fonts.googleapis.com/css2?family=Alfa+Slab+One&family=Bitter:wght@400;500&family=Mulish:wght@400;500;600&display=swap" rel="stylesheet">
<style>
:root{
  --stage:#58595b;
  --frame:#c6c6c6;
  --paper:#f7f6f3;
  --ink:#2f3a3c;
  --text:#222;
  --muted:#555;
  --blue:#3b7be8;
  --label:#1a1aff;
  --grey-btn:#9a9a9a;
  --white:#fff;
  --skyline:#dcdcdc;
  --coat:#b07a55;
  --hat:#7a4a35;
}
*{box-sizing:border-box;margin:0;padding:0}
html,body{width:742px;height:1200px;overflow:hidden;background:var(--stage)}
body{position:relative;font-family:"Mulish",sans-serif;color:var(--text)}
.screen{position:absolute;left:54px;width:644px;height:511px;background:var(--frame);padding:6px}
.screen--country{top:69px}
.screen--merchant{top:619px}
.paper{position:relative;width:100%;height:100%;background:var(--paper);overflow:hidden}
.skyline{position:absolute;left:0;right:0;bottom:0;height:95px;background:linear-gradient(to bottom,rgba(220,220,220,0),var(--skyline))}
.tower{position:absolute;right:12px;bottom:0;width:44px;height:150px;background:linear-gradient(to bottom,rgba(215,215,215,0),var(--skyline))}
.mascot-badge{position:absolute;left:571px;top:11px;width:59px;height:49px;border-radius:24px;background:linear-gradient(135deg,#3b8f98,#8a4b30)}
.detective{position:absolute;left:19px;top:320px;width:83px;height:173px;border-radius:30px 30px 6px 6px;background:linear-gradient(to bottom,var(--hat),var(--coat) 45%,#6b3f30)}
.title{position:absolute;top:42px;left:0;right:0;text-align:center;font-family:"Alfa Slab One",serif;font-size:31px;font-weight:400;letter-spacing:1px;color:var(--ink);text-transform:uppercase}
.tagline{position:absolute;top:98px;left:0;right:0;text-align:center;font-family:"Bitter",serif;font-size:11px;line-height:17.5px;color:var(--muted)}
.field-label{position:absolute;left:97px;top:155px;font-family:"Bitter",serif;font-size:8.5px;font-weight:500;color:var(--label)}
.search{position:absolute;left:98px;top:173px;width:440px;height:36px;border:1.5px solid var(--blue);border-radius:18px;background:var(--white);box-shadow:0 2px 6px rgba(59,123,232,.2);display:flex;align-items:center;justify-content:space-between;padding:0 10px 0 17px;font-size:7.6px;font-weight:500;letter-spacing:.1px}
.card{position:absolute;left:100px;width:436px;background:var(--white);border-radius:6px;box-shadow:0 2px 10px rgba(0,0,0,.05)}
.screen--country .card{top:249px;height:163px}
.screen--merchant .card{top:234px;height:228px}
.question{position:absolute;left:25px;top:20px;font-size:10px;font-weight:500}
.choices{position:absolute;left:25px;top:48px;display:flex;gap:18px;font-size:7.3px}
.choice{display:flex;align-items:center;gap:8px}
.radio{width:12px;height:12px;border:1.2px solid var(--blue);border-radius:50%}
.select{position:absolute;left:24px;top:80px;width:383px;height:28px;border:1.2px solid var(--blue);border-radius:14px;display:flex;align-items:center;padding:0 14px 0 10px;font-size:8.3px;gap:10px}
.flag{width:12px;height:12px;border-radius:50%;background:#1f3a8a;flex:none}
.select .caret{margin-left:auto}
.btn{position:absolute;top:127px;height:19px;border-radius:10px;color:var(--white);font-size:7.3px;display:flex;align-items:center;gap:5px;padding:0 9px}
.screen--merchant .btn{top:192px}
.btn--back{left:24px;width:45px;background:var(--grey-btn)}
.btn--next{right:28px;width:45px;background:var(--blue);justify-content:center}
.combo{position:absolute;left:25px;top:80px;width:258px;height:94px;border:1.2px solid var(--blue);border-radius:9px;overflow:hidden}
.combo-input{height:26px;border-bottom:1px solid var(--blue);display:flex;align-items:center;gap:8px;padding:0 11px;font-size:8.3px}
.combo-list{list-style:none;padding:7px 12px 0}
.combo-list li{display:flex;align-items:center;gap:8px;font-size:6.4px;height:14px}
.add-merchant{position:absolute;left:295px;top:80px;width:117px;height:28px;border-radius:14px;background:var(--blue);color:var(--white);font-family:"Bitter",serif;font-size:9px;display:flex;align-items:center;justify-content:center}
</style>
</head>
<body>

<section class="screen screen--country">
  <div class="paper">
    <div class="skyline" role="img" aria-label="Faint line drawing of a city skyline"></div>
    <div class="tower" role="img" aria-label="Faint line drawing of a skyscraper"></div>
    <div class="mascot-badge" role="img" aria-label="Illustration of spectacles and a moustache"></div>
    <h1 class="title">Fee Detective</h1>
    <p class="tagline">Helping you identify those odd and sometimes surprising charges<br>on your bank statements and transaction feeds!</p>
    <label class="field-label">Transaction Descriptor</label>
    <div class="search">
      <span>BRIMWELLS PTY LTD ST IVES AU</span>
      <svg width="20" height="20" viewBox="0 0 20 20"><circle cx="8" cy="8" r="6" fill="#e8f0f8" stroke="#555" stroke-width="1.4"/><line x1="12.5" y1="12.5" x2="17" y2="17" stroke="#e8892b" stroke-width="2.4" stroke-linecap="round"/></svg>
    </div>
    <div class="card">
      <p class="question">Do you know which country this merchant may be located in?</p>
      <div class="choices">
        <span class="choice"><span class="radio"></span>Your guess is as good as mine!</span>
        <span class="choice"><span class="radio"></span>I think they are in</span>
      </div>
      <div class="select">
        <span class="flag"></span>
        <span>AU - Australia</span>
        <svg class="caret" width="10" height="6" viewBox="0 0 10 6"><path d="M1 1l4 4 4-4" fill="none" stroke="#3b7be8" stroke-width="1.4"/></svg>
      </div>
      <span class="btn btn--back"><svg width="5" height="8" viewBox="0 0 5 8"><path d="M4 1L1 4l3 3" fill="none" stroke="#fff" stroke-width="1.3"/></svg>Back</span>
      <span class="btn btn--next">Next<svg width="5" height="8" viewBox="0 0 5 8"><path d="M1 1l3 3-3 3" fill="none" stroke="#fff" stroke-width="1.3"/></svg></span>
    </div>
    <div class="detective" role="img" aria-label="Illustration of a detective in a trench coat holding a magnifying glass"></div>
  </div>
</section>

<section class="screen screen--merchant">
  <div class="paper">
    <div class="skyline" role="img" aria-label="Faint line drawing of a city skyline"></div>
    <div class="tower" role="img" aria-label="Faint line drawing of a skyscraper"></div>
    <div class="mascot-badge" role="img" aria-label="Illustration of spectacles and a moustache"></div>
    <h1 class="title">Fee Detective</h1>
    <p class="tagline">Helping you identify those odd and sometimes surprising charges<br>on your bank statements and transaction feeds!</p>
    <label class="field-label">Transaction Descriptor</label>
    <div class="search">
      <span>BRIMWELLS PTY LTD ST IVES AU</span>
      <svg width="20" height="20" viewBox="0 0 20 20"><circle cx="8" cy="8" r="6" fill="#e8f0f8" stroke="#555" stroke-width="1.4"/><line x1="12.5" y1="12.5" x2="17" y2="17" stroke="#e8892b" stroke-width="2.4" stroke-linecap="round"/></svg>
    </div>
    <div class="card">
      <p class="question">Do you think you know who the merchant is?</p>
      <div class="choices">
        <span class="choice"><span class="radio"></span>Your guess is as good as mine!</span>
        <span class="choice"><span class="radio"></span>I think they may be</span>
      </div>
      <div class="combo">
        <div class="combo-input">
          <svg width="8" height="9" viewBox="0 0 8 9"><rect x=".5" y=".5" width="7" height="8" fill="none" stroke="#6a9be8"/><path d="M2 2h1M5 2h1M2 4h1M5 4h1M2 6h1M5 6h1" stroke="#6a9be8"/></svg>
          <span>Brimwel</span>
        </div>
        <ul class="combo-list">
          <li><svg width="6" height="7" viewBox="0 0 8 9"><rect x=".5" y=".5" width="7" height="8" fill="none" stroke="#777"/><path d="M2 2h1M5 2h1M2 4h1M5 4h1M2 6h1M5 6h1" stroke="#777"/></svg>Brimwells Pty Ltd</li>
          <li><svg width="6" height="7" viewBox="0 0 8 9"><rect x=".5" y=".5" width="7" height="8" fill="none" stroke="#777"/><path d="M2 2h1M5 2h1M2 4h1M5 4h1M2 6h1M5 6h1" stroke="#777"/></svg>Brimwells Online Plc</li>
          <li><svg width="6" height="7" viewBox="0 0 8 9"><rect x=".5" y=".5" width="7" height="8" fill="none" stroke="#777"/><path d="M2 2h1M5 2h1M2 4h1M5 4h1M2 6h1M5 6h1" stroke="#777"/></svg>Brimwerks Pty Ltd</li>
          <li><svg width="6" height="7" viewBox="0 0 8 9"><rect x=".5" y=".5" width="7" height="8" fill="none" stroke="#777"/><path d="M2 2h1M5 2h1M2 4h1M5 4h1M2 6h1M5 6h1" stroke="#777"/></svg>Brimwold Ltd</li>
        </ul>
      </div>
      <span class="add-merchant">Add New Merchant</span>
      <span class="btn btn--back"><svg width="5" height="8" viewBox="0 0 5 8"><path d="M4 1L1 4l3 3" fill="none" stroke="#fff" stroke-width="1.3"/></svg>Back</span>
      <span class="btn btn--next">Next<svg width="5" height="8" viewBox="0 0 5 8"><path d="M1 1l3 3-3 3" fill="none" stroke="#fff" stroke-width="1.3"/></svg></span>
    </div>
    <div class="detective" role="img" aria-label="Illustration of a detective in a trench coat holding a magnifying glass"></div>
  </div>
</section>

</body>
</html>
```